Profesional personal website needs design and business card

I need a business card with my professional name as a logo "Dorian Vitality" for my business. I am a Wellness Coach, consultant and trainer. So it should be professional, wellness oriented and modern.

Target Market(s)

Private clients, governments, corporations. Luxury and high market.

Industry/Entity Type

Health And Wellness

Contact Information for Business Card

Dorian Vitality should be the logo

Colors

Designer to choose colors to be used in the design.

Requirements
Must have
• Dorian Vitality
• Name: Tomás Lirandel
• Wellness Coach, Consultant & Trainer.
• Website: www.dorianvitality-example.com
• Phone:
• Spain (+34) 612 480 317
• (USA) +1 (555) 610 4829
Nice to have
• The most important is the design of "Dorian Vitality", as this is going to be my personal brand logo. It should be professional, wellness, high end and actual.
Should not have
• no golds, no baroque style..

```html
<!DOCTYPE html>
<html lang="en">
<head>
<meta charset="utf-8">
<title>Dorian Vitality — Business Card</title>
<link href="https://fonts.googleapis.com/css2?family=Lato:wght@400;700;900&display=swap" rel="stylesheet">
<style>
  :root{
    --navy:#0a4a78;
    --ink:#1f1f1f;
    --paper:#ffffff;
    --bg:#ffffff;
    --shadow:rgba(0,0,0,0.28);
  }
  *{margin:0;padding:0;box-sizing:border-box;}
  html,body{width:1200px;height:1200px;overflow:hidden;background:var(--bg);}
  body{position:relative;font-family:"Lato",sans-serif;}

  .card{position:absolute;left:180px;width:840px;height:478px;border-radius:22px;overflow:hidden;
        box-shadow:6px 6px 8px var(--shadow);}
  .card--front{top:82px;background:var(--paper);}
  .card--back{top:639px;background:var(--navy);}

  .brand{position:absolute;display:flex;align-items:center;gap:12px;font-weight:900;
         letter-spacing:0.5px;white-space:nowrap;font-family:"Lato",sans-serif;}
  .brand__square{width:14px;height:14px;}
  .card--front .brand{left:43px;top:44px;font-size:40px;color:var(--navy);}
  .card--front .brand__square{background:var(--navy);}
  .card--back .brand{left:0;right:0;top:210px;justify-content:center;font-size:52px;color:var(--paper);}
  .card--back .brand__square{background:var(--paper);width:18px;height:18px;}

  .accent-tab{position:absolute;left:0;top:257px;width:13px;height:51px;background:var(--navy);
              border-radius:0 5px 5px 0;}

  .holder{position:absolute;left:42px;top:248px;}
  .holder__name{font-size:38px;font-weight:700;color:var(--navy);line-height:1;letter-spacing:-0.3px;}
  .holder__role{margin-top:8px;font-size:18.5px;font-weight:700;color:var(--ink);}

  .contacts{position:absolute;left:43px;top:341px;list-style:none;}
  .contacts li{display:flex;align-items:center;height:30px;font-size:19px;color:var(--ink);}
  .contacts svg{width:19px;height:19px;margin-right:8px;fill:var(--navy);flex:none;}
  .contacts .tag{color:var(--navy);margin-left:6px;}

  .notch{position:absolute;top:142px;width:13px;height:197px;background:var(--bg);}
  .notch--left{left:0;border-radius:0 5px 5px 0;}
  .notch--right{right:0;border-radius:5px 0 0 5px;}

  .back-web{position:absolute;left:0;right:0;top:424px;text-align:center;font-size:19px;color:var(--paper);}
</style>
</head>
<body>

<section class="card card--front">
  <div class="brand"><span class="brand__square"></span>DORIAN VITALITY</div>
  <div class="accent-tab"></div>
  <div class="holder">
    <h1 class="holder__name">Tomás Lirandel</h1>
    <p class="holder__role">Wellness Coach, Consultant &amp; Trainer</p>
  </div>
  <ul class="contacts">
    <li>
      <svg viewBox="0 0 24 24" aria-hidden="true"><path d="M6.6 2.5 9.5 6.8c.4.6.3 1.3-.2 1.8L7.6 10.2c1.3 2.7 3.5 4.9 6.2 6.2l1.6-1.7c.5-.5 1.2-.6 1.8-.2l4.3 2.9c.6.4.8 1.2.4 1.8l-1.4 2.3c-.5.8-1.5 1.2-2.4.9C10.6 20.3 3.7 13.4 1.6 5.9c-.3-.9.1-1.9.9-2.4l2.3-1.4c.6-.4 1.4-.2 1.8.4z"/></svg>
      (+34) 612 480 317<span class="tag">Spain</span>
    </li>
    <li>
      <svg viewBox="0 0 24 24" aria-hidden="true"><path d="M7 1h10a2 2 0 0 1 2 2v18a2 2 0 0 1-2 2H7a2 2 0 0 1-2-2V3a2 2 0 0 1 2-2zm0 3v14h10V4H7zm5 15.2a1.2 1.2 0 1 0 0 2.4 1.2 1.2 0 0 0 0-2.4z"/></svg>
      +1 (555) 610 4829<span class="tag">(USA)</span>
    </li>
    <li>
      <svg viewBox="0 0 24 24" aria-hidden="true"><path d="M12 2a10 10 0 1 0 0 20 10 10 0 0 0 0-20zm0 2c.9 0 2.2 1.7 2.8 5H9.2C9.8 5.7 11.1 4 12 4zM4.3 10h2.9a17 17 0 0 0 0 4H4.3a8 8 0 0 1 0-4zm.9 6h2.3c.3 1.3.8 2.5 1.3 3.4A8 8 0 0 1 5.2 16zm2.3-8H5.2a8 8 0 0 1 3.6-3.4c-.5.9-1 2.1-1.3 3.4zM12 20c-.9 0-2.2-1.7-2.8-4h5.6c-.6 2.3-1.9 4-2.8 4zm3-6H9a15 15 0 0 1 0-4h6a15 15 0 0 1 0 4zm.2 5.4c.5-.9 1-2.1 1.3-3.4h2.3a8 8 0 0 1-3.6 3.4zM16.8 14a17 17 0 0 0 0-4h2.9a8 8 0 0 1 0 4h-2.9zm-.3-6c-.3-1.3-.8-2.5-1.3-3.4A8 8 0 0 1 18.8 8h-2.3z"/></svg>
      www.dorianvitality-example.com
    </li>
  </ul>
</section>

<section class="card card--back">
  <div class="notch notch--left"></div>
  <div class="notch notch--right"></div>
  <div class="brand"><span class="brand__square"></span>DORIAN VITALITY</div>
  <p class="back-web">www.dorianvitality-example.com</p>
</section>

</body>
</html>
```